Business Card Update, need to bring life to the card, two sided color

We need a new business card design, are moving and changing addresses and need a new look, we have the logos already attached but need a new style moving forward. Can incorporate the color of the logo (The Green) as well, maybe a solid back? We deal with safety products revolving around static electricity and safety lighting. Would like to keep same font in second logo as well.

Target Market(s)

Electrical Safety, Lighting

Contact Information for Business Card

Dale Fenwick
Vice President
Office: 770-555-4821
Cell: 770-555-3067
dale@tkfenwick.example
www.tkfenwick.example
4700 West Harbor Boulevard
Suite #150
Roswell, GA 30076

Font styles to use
Serif
Sans Serif

Requirements
Must have
• Since 1918
Nice to have
• Could use the 100 Year Logo for back of card, would like the back of card to be the same green as logo.
Should not have
• No black cards please.

```html
<!DOCTYPE html>
<html lang="en">
<head>
<meta charset="utf-8">
<title>T.K. Fenwick Business Card</title>
<link href="https://fonts.googleapis.com/css2?family=Arimo:wght@400;700&display=swap" rel="stylesheet">
<style>
  :root {
    --green: #07995a;
    --white: #ffffff;
    --ink: #555a5c;
    --backdrop: #e9ebea;
  }
  * { margin: 0; padding: 0; box-sizing: border-box; }
  html, body {
    width: 1200px; height: 800px; overflow: hidden;
    background: var(--backdrop);
    font-family: "Arimo", Arial, sans-serif;
  }
  .sheet {
    width: 1200px; height: 800px;
    display: flex; align-items: center; justify-content: center; gap: 40px;
  }
  .card {
    position: relative; width: 540px; height: 309px; overflow: hidden;
    box-shadow: 0 6px 18px rgba(0,0,0,0.15);
  }
  /* back side */
  .card-back { background: var(--green); color: var(--white); }
  .back-mark {
    position: absolute; left: 50%; top: 62px; transform: translateX(-50%);
    display: flex; flex-direction: column; align-items: center; gap: 8px;
  }
  .back-mark .dot {
    width: 70px; height: 70px; border-radius: 50%; border: 5px solid var(--white);
  }
  .back-mark .mark-name { font-weight: 700; font-size: 18px; letter-spacing: 1px; }
  .back-mark .since { font-weight: 700; font-size: 12px; letter-spacing: 2px; }
  .back-url {
    position: absolute; left: 0; right: 0; top: 232px; text-align: center;
    font-weight: 700; font-size: 14px; letter-spacing: 0.5px;
  }
  /* front side */
  .card-front { background: var(--white); }
  .front-mark {
    position: absolute; left: 34px; top: 44px; width: 112px; height: 112px;
    border-radius: 50%; background: var(--green);
  }
  .company {
    position: absolute; left: 164px; top: 58px; color: var(--green);
  }
  .company-name { font-weight: 700; font-size: 33px; line-height: 1; letter-spacing: -0.5px; }
  .company-sub { font-weight: 700; font-size: 14px; margin-top: 4px; }
  .company-since { font-weight: 700; font-size: 11px; letter-spacing: 1.5px; margin-top: 5px; }
  .name-band {
    position: absolute; left: 0; right: 0; top: 166px; height: 44px;
    background: var(--green); color: var(--white);
    display: flex; align-items: baseline; justify-content: center; gap: 10px;
    padding-top: 12px;
  }
  .person-name { font-weight: 700; font-size: 20px; }
  .person-title { font-size: 13px; }
  .contacts {
    position: absolute; top: 220px; left: 60px; width: 262px;
    display: flex; flex-direction: column; gap: 2px;
    color: var(--ink); font-size: 12px; line-height: 15px; text-align: right;
  }
  .contact-row { display: flex; justify-content: flex-end; align-items: center; gap: 8px; }
  .contact-row svg { width: 12px; height: 12px; flex: none; }
  .divider {
    position: absolute; left: 336px; top: 222px; width: 1px; height: 62px; background: var(--green);
  }
  .address {
    position: absolute; left: 350px; top: 222px; color: var(--ink); font-size: 12px; line-height: 17px;
  }
  .bottom-stripe {
    position: absolute; left: 0; right: 0; bottom: 0; height: 10px; background: var(--green);
  }
</style>
</head>
<body>
<main class="sheet">
  <section class="card card-back" aria-label="Card back">
    <div class="back-mark">
      <span class="dot"></span>
      <span class="mark-name">T.K. FENWICK</span>
      <span class="since">SINCE 1918</span>
    </div>
    <p class="back-url">www.tkfenwick.example</p>
  </section>

  <section class="card card-front" aria-label="Card front">
    <span class="front-mark"></span>
    <div class="company">
      <p class="company-name">T.K. Fenwick</p>
      <p class="company-sub">Manufacturing Company, Inc.</p>
      <p class="company-since">SINCE 1918</p>
    </div>
    <div class="name-band">
      <span class="person-name">Dale Fenwick</span>
      <span class="person-title">Vice President</span>
    </div>
    <div class="contacts">
      <p class="contact-row">Office: 770-555-4821
        <svg viewBox="0 0 12 12"><path d="M2.5 1.5 L4.5 1.5 L5.3 4 L4 5 Q5 7.2 7 8 L8 6.7 L10.5 7.5 L10.5 9.5 Q10 10.5 9 10.5 Q2 10 1.5 3 Q1.5 2 2.5 1.5 Z" fill="#07995a"/></svg>
      </p>
      <p class="contact-row">Cell: 770-555-3067
        <svg viewBox="0 0 12 12"><rect x="2.5" y="1" width="7" height="10" rx="1" fill="none" stroke="#07995a" stroke-width="1.4"/></svg>
      </p>
      <p class="contact-row">dale@tkfenwick.example
        <svg viewBox="0 0 12 12"><rect x="1" y="2.5" width="10" height="7" fill="#07995a"/><path d="M1 2.5 L6 6.5 L11 2.5" fill="none" stroke="#fff" stroke-width="1"/></svg>
      </p>
      <p class="contact-row">www.tkfenwick.example
        <svg viewBox="0 0 12 12"><circle cx="6" cy="6" r="5.5" fill="#07995a"/><path d="M0.5 6 H11.5 M6 0.5 V11.5" stroke="#fff" stroke-width="0.8"/><ellipse cx="6" cy="6" rx="2.4" ry="5.5" fill="none" stroke="#fff" stroke-width="0.8"/></svg>
      </p>
    </div>
    <span class="divider"></span>
    <p class="address">4700 West Harbor Boulevard<br>Suite #150<br>Roswell, GA 30076</p>
    <span class="bottom-stripe"></span>
  </section>
</main>
</body>
</html>
```